Tidy4all

Full service cleaning company. Specializing in commercial and apartment cleans.
Fully licensed and insured
Digital photos and invoices provided
for every job
For web designer...basic info as expected by a highend cleaning company that provides excellent service at reasonable pricing. We are going after large property management companies as well as not pricing ourselves out to help the local mom and pop companies as well.
Updates

Project Deadline Extended Reason: Everyone seems to be having trouble understanding that we are a dumpster company that is adding a cleaning side to the company. We want our clients to see Tidy4All as a separate branch of our our already established waste management company.We are not a regular cleaning company. We specialize in going after large commercial cleans and apartment cleans. I have now included info regarding a proposal for work and our invoice/job completion to make it clearer what we do Added Monday, July 20, 2015

Target Market(s)

Property Management companies in Savannah, Richmond Hill, Rincon, Hinesville and Midway Georgia

Industry/Entity Type

Cleaning Service

Coding

Coded - Design and coding required

Number of Pages Required

3 page

Requirements
Must have
• Nice home page with lots of photos (stock are fine) to convey exactly what we do (getting logo bid on right now on this sight).
• Information page with employee photos (can leave blank) need room for 4 photos and bios.
• Page or link to a static page for the dumpster company BinRun (logo for this is red and black file attached along with photo of dumpster. This page just needs to be one page with contact info and information about commercial dumpster.
• Basically this site is just a fluff page used for marketing purposes. Its content can be general and once created wont change much. Services and photos can be provided upon request but general layout and info is what we are looking for.

```html
<!DOCTYPE html>
<html lang="en">
<head>
<meta charset="utf-8">
<title>Tidy4All</title>
<link href="https://fonts.googleapis.com/css2?family=Oswald:wght@400;500;600&family=Open+Sans:wght@400;600;700&display=swap" rel="stylesheet">
<style>
:root{
  --red:#e3171b;
  --dark:#1d1d1d;
  --darker:#111;
  --text:#555;
  --light:#f2f2f2;
  --white:#fff;
  --line:#d8d8d8;
}
*{box-sizing:border-box;margin:0;padding:0}
html,body{width:726px;height:1200px;overflow:hidden;background:var(--white)}
body{font-family:"Open Sans",Arial,sans-serif;color:var(--text);font-size:7px;line-height:1.45}
.page{width:726px;height:1200px;position:relative}
h2,h3,.nav a,.btn,.card-label,.cta-text{font-family:"Oswald",Arial,sans-serif}

/* header */
.site-header{height:72px;display:flex;position:relative}
.brand{width:200px;display:flex;align-items:center;gap:8px;padding-left:32px}
.brand-mark{width:22px;height:22px;background:var(--red)}
.brand-name{font-family:"Open Sans",Arial,sans-serif;font-weight:700;font-size:24px;color:var(--red)}
.header-right{flex:1;display:flex;flex-direction:column}
.topbar{height:22px;background:var(--red);margin-left:230px;display:flex;justify-content:flex-end;align-items:center;gap:20px;padding-right:32px;color:var(--white);font-size:8px}
.topbar span{display:flex;align-items:center;gap:4px}
.nav{height:40px;background:var(--darker);margin-top:4px;display:flex;align-items:center;padding-left:40px}
.nav a{color:var(--white);text-decoration:none;font-size:9px;padding:0 16px;height:40px;line-height:40px}
.nav a.active{background:var(--red)}

/* hero */
.hero{height:292px;position:relative;background:linear-gradient(90deg,#5b7a3e 0%,#2f6a9a 45%,#9fb8cf 70%,#6f8aa6 100%)}
.hero-copy{position:absolute;left:330px;top:100px;color:var(--white);font-family:"Oswald",Arial,sans-serif;font-weight:600;font-size:19px;line-height:1.25;background:rgba(0,0,0,.45);padding:8px 14px}

/* welcome */
.intro{display:flex;padding:30px 38px 0;gap:40px;height:240px}
.welcome{flex:1}
h2{font-size:16px;font-weight:500;color:#222;position:relative;padding-bottom:8px;margin-bottom:12px}
h2::after{content:"";position:absolute;left:0;bottom:0;width:40px;height:2px;background:var(--red)}
h2 em{color:var(--red);font-style:normal}
.welcome p{margin-bottom:9px}
.btn{display:inline-block;background:var(--red);color:var(--white);font-size:8px;padding:5px 10px;border:0;text-decoration:none}
.schedule{width:200px}
.field{border:1px solid var(--line);height:20px;font-size:6.5px;color:#888;padding:5px 6px;margin-bottom:5px}
.field.row{display:flex;gap:5px;border:0;padding:0}
.field.row span{flex:1;border:1px solid var(--line);padding:5px 6px}
.field.msg{height:34px}

/* cards */
.cards{background:var(--dark);height:150px;margin-top:10px;padding:20px 38px;display:flex;gap:24px}
.card{flex:1;position:relative;height:110px}
.card-photo{height:100%}
.card-label{position:absolute;left:0;bottom:6px;background:var(--red);color:var(--white);font-size:11px;padding:3px 10px}
.card-label small{display:block;font-family:"Open Sans",Arial,sans-serif;font-size:6px}

/* features */
.features{display:flex;gap:28px;padding:26px 38px 0;height:222px}
.feature{flex:1}
.feature-photo{height:70px;margin-bottom:8px}
.ticks{list-style:none}
.ticks li{display:flex;align-items:center;gap:6px;margin-bottom:9px;font-size:7.5px}

/* cta */
.cta{background:var(--red);height:40px;display:flex;align-items:center;padding:0 38px;gap:14px}
.cta-text{color:var(--white);font-size:11px;font-weight:500;flex:1}
.cta-input{width:140px;height:20px;background:var(--white);font-size:6.5px;color:#888;padding:5px 6px}
.cta .btn{background:var(--darker);height:20px;line-height:10px}

/* footer */
.site-footer{background:var(--dark);height:154px;padding:18px 38px;display:flex;gap:30px;color:#ccc}
.site-footer h3{color:var(--white);font-size:10px;font-weight:500;margin-bottom:8px}
.site-footer ul{list-style:none}
.site-footer li{margin-bottom:4px;display:flex;gap:5px;align-items:flex-start}
.foot-links{width:120px}
.foot-contact{width:150px}
.foot-faq{flex:1}
.foot-brand{width:120px;display:flex;align-items:center;gap:6px;color:#bbb;font-weight:700;font-size:18px}
.foot-brand i{width:16px;height:16px;background:#bbb;display:block}
.bottombar{background:var(--darker);height:22px;display:flex;align-items:center;justify-content:space-between;padding:0 38px;color:#aaa;font-size:6.5px}
.social{display:flex;gap:5px}
.social i{width:11px;height:11px;background:#ddd;display:block}
</style>
</head>
<body>
<div class="page">
  <header class="site-header">
    <div class="brand"><span class="brand-mark"></span><span class="brand-name">Tidy4All</span></div>
    <div class="header-right">
      <div class="topbar">
        <span><svg width="8" height="6" viewBox="0 0 8 6"><rect x=".5" y=".5" width="7" height="5" fill="none" stroke="#fff"/><path d="M.5 .5 4 3.5 7.5 .5" fill="none" stroke="#fff"/></svg>info@tidy4all.com</span>
        <span><svg width="7" height="7" viewBox="0 0 7 7"><path d="M1 0h2l.5 2-1 1a4 4 0 0 0 1.5 1.5l1-1 2 .5v2a1 1 0 0 1-1 1A6 6 0 0 1 0 1a1 1 0 0 1 1-1z" fill="#fff"/></svg>555 010 2030</span>
      </div>
      <nav class="nav">
        <a class="active">Home</a><a>About Us</a><a>Services</a><a>Think Green</a><a>Customer Reviews</a><a>Contact Us</a>
      </nav>
    </div>
  </header>

  <section class="hero" role="img" aria-label="Refuse truck lifting a blue dumpster beside tall city office towers">
    <div class="hero-copy">We Are A Full Service<br>Cleaning Company<br>Specializing in commercial<br>and apartment cleans</div>
  </section>

  <section class="intro">
    <div class="welcome">
      <h2>Welcome To <em>Tidy4All</em></h2>
      <p>Lorem ipsum dolor sit amet, consectetuer adipiscing elit, sed diam nonummy nibh euismod tincidunt ut laoreet dolore magna aliquam erat volutpat. Ut wisi enim ad minim veniam, quis nostrud exerci tation ullamcorper suscipit lobortis nisl ut aliquip ex ea commodo consequat. Duis autem vel eum iriure dolor in hendrerit in vulputate velit esse molestie consequat, vel illum dolore eu feugiat nulla facilisis at vero eros et accumsan et iusto odio dignissim qui blandit praesent luptatum zzril delenit augue duis dolore te feugait nulla facilisi.</p>
      <p>Lorem ipsum dolor sit amet, consectetuer adipiscing elit, sed diam nonummy nibh euismod tincidunt ut laoreet dolore magna aliquam erat volutpat.</p>
      <a class="btn">READ MORE</a>
    </div>
    <form class="schedule">
      <h2>Schedule A Service</h2>
      <div class="field">Name</div>
      <div class="field">Phone</div>
      <div class="field">Pick up Date &amp; Time</div>
      <div class="field row"><span>Pick up Date</span><span>Start</span><span>Time</span></div>
      <div class="field msg">Message</div>
      <span class="btn">SUBMIT</span>
    </form>
  </section>

  <section class="cards">
    <div class="card"><div class="card-photo" role="img" aria-label="Modern family home exterior" style="background:linear-gradient(135deg,#8a6a4a,#c9b79a 60%,#5d7a4a)"></div><div class="card-label">Home Owner<small>Read More ›</small></div></div>
    <div class="card"><div class="card-photo" role="img" aria-label="Green refuse truck on a street" style="background:linear-gradient(135deg,#3d5a3a,#7d9a6e 55%,#b5bfae)"></div><div class="card-label">Business Owner<small>Read More ›</small></div></div>
    <div class="card"><div class="card-photo" role="img" aria-label="Large roll-off dumpster on a truck" style="background:linear-gradient(135deg,#6c7e8e,#b9c4cc 55%,#8e9aa2)"></div><div class="card-label">Rent-a-Dumpster<small>Read More ›</small></div></div>
  </section>

  <section class="features">
    <div class="feature">
      <h2>24/7 Access</h2>
      <div class="feature-photo" role="img" aria-label="24 hour service sign" style="background:linear-gradient(135deg,#3a3a3a,#9a9a9a)"></div>
      <p>Lorem ipsum dolor sit amet consectetuer adipiscing elit sed diam nonummy nibh euismod tincidunt ut laoreet dolore magna aliquam erat.</p>
    </div>
    <div class="feature">
      <h2>Reliable. Clean. Safe.</h2>
      <div class="feature-photo" role="img" aria-label="Row of green wheeled waste bins" style="background:linear-gradient(135deg,#2f6a2a,#7fb24a 60%,#c8d8c0)"></div>
      <p>Lorem ipsum dolor sit amet consectetuer adipiscing elit sed diam nonummy nibh euismod tincidunt ut laoreet dolore magna aliquam erat.</p>
    </div>
    <div class="feature">
      <h2>Why Choose Us</h2>
      <ul class="ticks">
        <li><svg width="8" height="8" viewBox="0 0 8 8"><circle cx="4" cy="4" r="4" fill="#e3171b"/><path d="M2 4l1.5 1.5L6 2.7" stroke="#fff" fill="none"/></svg>Wide selection of dumpster sizes available</li>
        <li><svg width="8" height="8" viewBox="0 0 8 8"><circle cx="4" cy="4" r="4" fill="#e3171b"/><path d="M2 4l1.5 1.5L6 2.7" stroke="#fff" fill="none"/></svg>Flexible, Timely pickup and delivery</li>
        <li><svg width="8" height="8" viewBox="0 0 8 8"><circle cx="4" cy="4" r="4" fill="#e3171b"/><path d="M2 4l1.5 1.5L6 2.7" stroke="#fff" fill="none"/></svg>Fresh service available</li>
        <li><svg width="8" height="8" viewBox="0 0 8 8"><circle cx="4" cy="4" r="4" fill="#e3171b"/><path d="M2 4l1.5 1.5L6 2.7" stroke="#fff" fill="none"/></svg>Easy online ordering and scheduling</li>
        <li><svg width="8" height="8" viewBox="0 0 8 8"><circle cx="4" cy="4" r="4" fill="#e3171b"/><path d="M2 4l1.5 1.5L6 2.7" stroke="#fff" fill="none"/></svg>Online account management</li>
        <li><svg width="8" height="8" viewBox="0 0 8 8"><circle cx="4" cy="4" r="4" fill="#e3171b"/><path d="M2 4l1.5 1.5L6 2.7" stroke="#fff" fill="none"/></svg>Instant online pricing</li>
      </ul>
    </div>
  </section>

  <section class="cta">
    <div class="cta-text">Ready To Get Started? See What Dumpsters Are Available In Your Area.</div>
    <div class="cta-input">Enter Zip Code or Post Code</div>
    <span class="btn">SHOW PRODUCTS</span>
  </section>

  <footer class="site-footer">
    <div class="foot-links">
      <h3>Quick Links</h3>
      <ul><li>› Home</li><li>› About Us</li><li>› Services</li><li>› Think Green</li><li>› Customer Reviews</li><li>› Contact Us</li></ul>
    </div>
    <div class="foot-contact">
      <h3>Contact Information</h3>
      <ul>
        <li><svg width="7" height="9" viewBox="0 0 7 9"><path d="M3.5 0A3.5 3.5 0 0 0 0 3.5C0 6 3.5 9 3.5 9S7 6 7 3.5A3.5 3.5 0 0 0 3.5 0z" fill="#e3171b"/><circle cx="3.5" cy="3.5" r="1.2" fill="#1d1d1d"/></svg>418 Harbor Lane, Suite 2,<br>Elmford, ZZ 00000</li>
        <li><svg width="7" height="7" viewBox="0 0 7 7"><path d="M1 0h2l.5 2-1 1a4 4 0 0 0 1.5 1.5l1-1 2 .5v2a1 1 0 0 1-1 1A6 6 0 0 1 0 1a1 1 0 0 1 1-1z" fill="#e3171b"/></svg>555 010 2030</li>
        <li><svg width="8" height="6" viewBox="0 0 8 6"><rect x=".5" y=".5" width="7" height="5" fill="none" stroke="#e3171b"/><path d="M.5 .5 4 3.5 7.5 .5" fill="none" stroke="#e3171b"/></svg>info@tidy4all.com</li>
      </ul>
    </div>
    <div class="foot-faq">
      <h3>FAQ's</h3>
      <ul><li>› What sizes of dumpsters do you offer?</li><li>› How much does a dumpster cost?</li><li>› How much does a delivery take?</li><li>› How long can we keep the dumpster?</li><li style="color:#fff">More FAQ's</li></ul>
    </div>
    <div class="foot-brand"><i></i>Tidy4All</div>
  </footer>
  <div class="bottombar">
    <span>© 2015 Tidy4All, All Rights Reserved.</span>
    <span class="social"><i></i><i></i><i></i></span>
  </div>
</div>
</body>
</html>
```